Highlight Document Over Image for Slide

We are seeking a graphic designer to overlay a news article on an image that pertains to the article, aiming for a stylish yet professional appearance. Given the limited resources, we encourage you to use your imagination and go beyond what basic tools like PowerPoint can offer.

```html
<!DOCTYPE html>
<html lang="en">
<head>
<meta charset="utf-8">
<title>Introduction or Possession of Contraband Items</title>
<link rel="stylesheet" href="https://fonts.googleapis.com/css2?family=Tinos:wght@400;700&display=swap">
<style>
  :root {
    --canvas-bg: #efefef;
    --ink: #111111;
    --muted-ink: #6b6b6b;
    --rule: #4a4a4a;
    --earth-light: #b59a6c;
    --earth-mid: #8a7456;
    --roof-gray: #6f6a63;
    --water: #6e6c64;
    --water-deep: #5d5b55;
    --fade-white: rgba(255,255,255,0.97);
  }
  * { margin: 0; padding: 0; box-sizing: border-box; }
  html, body {
    width: 1200px; height: 1200px; overflow: hidden;
    background: var(--canvas-bg);
  }
  .slide {
    position: absolute;
    left: 25px; top: 242px;
    width: 1155px; height: 649px;
    overflow: hidden;
    box-shadow: 0 3px 10px rgba(0,0,0,0.45);
  }
  .aerial-view {
    position: absolute; inset: 0;
    background:
      radial-gradient(ellipse 40% 45% at 45% 50%, var(--roof-gray) 0%, rgba(111,106,99,0.6) 50%, rgba(111,106,99,0) 100%),
      linear-gradient(180deg, var(--earth-light) 0%, var(--earth-mid) 45%, var(--water) 72%, var(--water-deep) 100%);
  }
  .text-fade {
    position: absolute; inset: 0;
    background:
      radial-gradient(ellipse 38% 62% at 80% 40%, var(--fade-white) 0%, rgba(255,255,255,0.92) 55%, rgba(255,255,255,0) 100%);
  }
  .notice {
    position: absolute;
    left: 718px; top: 80px;
    width: 397px;
    font-family: "Tinos", "Times New Roman", serif;
    color: var(--ink);
  }
  .notice-title {
    font-weight: 700;
    font-size: 19px;
    line-height: 26px;
    text-align: center;
    margin-left: 20px;
    width: 355px;
  }
  .notice-rule {
    border: 0;
    border-top: 1px solid var(--rule);
    width: 341px;
    margin: 15px 0 0 30px;
  }
  .notice-body {
    font-size: 18.4px;
    line-height: 26.2px;
    text-align: justify;
    margin-top: 12px;
  }
  .notice-rule.bottom { margin-top: 26px; margin-left: 27px; }
  .page-number {
    font-weight: 700;
    font-size: 18px;
    color: var(--muted-ink);
    text-align: center;
    margin: 25px 0 0 60px;
  }
</style>
</head>
<body>
  <section class="slide">
    <div class="aerial-view" role="img" aria-label="Aerial photograph of a waterfront correctional facility with buildings, yards and roads beside the bay"></div>
    <div class="text-fade"></div>
    <article class="notice">
      <h1 class="notice-title">INTRODUCTION OR POSSESSION OF CONTRABAND ITEMS</h1>
      <hr class="notice-rule">
      <p class="notice-body">Employees shall not introduce or possess unauthorized items such as escape paraphernalia, weapons, facsimiles of weapons, ammunition, wireless communication devices, cell phones, tobacco or facsimiles of tobaccos products (e.g. electronic vapor cigarettes) lighters or any other item not specifically authorized by PD 04.04.100 “Custody, Security and Safety Systems (Exempt)”, OP 04.04.100 “Gate Security” or facility operating procedure in any facility where offenders are housed. Employees are responsible for any item in their</p>
      <hr class="notice-rule bottom">
      <p class="page-number">36</p>
    </article>
  </section>
</body>
</html>
```